Business Cards Needed for Innovative Healthcare Marketing Company

We are a marketing company focused on healthcare. Our company is all about rebranding yourself renewing your image and generating results. The phoenix stands for "reborn" or "rising" which we provide new brands for our clients we take their old brands and renew it with creativity and innovation. I am looking for a business card with color dimension. I have attached an example of a card I think has the look and feel of what I am trying to accomplish. I like that the card example has black and grey font colors, I like the font placement and the small logo, I really like the use of the colors on the right those are the colors of my logo. My logo is phoenix so maybe incorporating flames similar to that design. I would like the back a solid color maybe red with an opaque version of the logo and website. As a marketing company I am always open to creative liberty!

Target Market(s)

Doctors and business professionals.

Industry/Entity Type

Marketing

Contact Information for Business Card

Valcorne Health Care Marketing
Marla Tenwick- CEO
#(512)638-2974
email-marla@valcorne.com
website- valcorne.com

Font styles to use
Sans Serif

Colors
ec1f27
f37122
ffc214
fbed22
fbf289
f04a50

Requirements
Must have
• The logo and required information
Nice to have
• icons by the information
Should not have
• child like font

```html
<!DOCTYPE html>
<html lang="en">
<head>
<meta charset="utf-8">
<title>Valcorne Health Care Marketing – Business Card</title>
<link rel="stylesheet" href="https://fonts.googleapis.com/css2?family=Open+Sans:wght@400;700&family=Raleway:wght@300;400&display=swap">
<style>
  :root {
    --backdrop: #3a3a3a;
    --card-white: #ffffff;
    --brand-red: #a81c22;
    --brand-red-deep: #8e1418;
    --brand-orange: #f37122;
    --brand-amber: #f5a021;
    --brand-gold: #ffc214;
    --ink-grey: #4a4a4a;
    --ink-soft: #8a8a8a;
    --icon-red: #c4262c;
  }
  * { box-sizing: border-box; margin: 0; padding: 0; }
  html, body { width: 1200px; height: 950px; overflow: hidden; }
  body {
    background: var(--backdrop);
    display: flex;
    flex-direction: column;
    align-items: center;
    justify-content: center;
    gap: 40px;
    font-family: "Open Sans", sans-serif;
  }
  .card {
    position: relative;
    width: 760px;
    height: 434px;
    border-radius: 26px;
    overflow: hidden;
  }
  /* Front */
  .card--front { background: var(--card-white); }
  .front-band { position: absolute; inset: 0; width: 100%; height: 100%; }
  .brand {
    position: absolute;
    left: 60px;
    top: 92px;
    display: flex;
    align-items: center;
    gap: 22px;
  }
  .brand-mark {
    width: 96px; height: 96px; border-radius: 50%;
    background: radial-gradient(circle at 40% 40%, var(--brand-gold), var(--brand-orange) 55%, var(--brand-red));
  }
  .brand-name {
    font-family: "Raleway", sans-serif;
    font-weight: 300;
    color: var(--brand-red);
    line-height: 1.1;
  }
  .brand-name .word { display: block; font-size: 52px; letter-spacing: 4px; text-transform: uppercase; }
  .brand-name .tag { display: block; font-size: 15px; letter-spacing: 3.2px; text-transform: uppercase; border-top: 1px solid var(--brand-red); padding-top: 5px; margin-top: 4px; }
  .person { position: absolute; left: 178px; top: 246px; }
  .person-name { font-weight: 700; font-size: 27px; color: var(--brand-red); }
  .person-role { font-weight: 700; font-size: 19px; color: var(--brand-amber); margin-top: 2px; }
  .contacts {
    position: absolute; left: 400px; top: 246px;
    list-style: none; font-size: 17px; color: var(--ink-grey);
  }
  .contacts li { display: flex; align-items: center; gap: 12px; margin-bottom: 10px; }
  .contacts svg { width: 17px; height: 17px; fill: var(--icon-red); flex: none; }
  /* Back */
  .card--back {
    background: radial-gradient(ellipse at 45% 42%, #f5941f 0%, var(--brand-orange) 38%, #d43c1e 70%, var(--brand-red-deep) 100%);
    display: flex; align-items: center; justify-content: center; gap: 30px;
  }
  .card--back .brand-mark {
    width: 120px; height: 120px;
    background: rgba(255,255,255,0.9);
  }
  .card--back .brand-name { color: #ffffff; }
  .card--back .brand-name .word { font-size: 64px; }
  .card--back .brand-name .tag { font-size: 18px; border-top-color: #ffffff; }
</style>
</head>
<body>
  <section class="card card--front" aria-label="Business card front">
    <svg class="front-band" viewBox="0 0 760 434" preserveAspectRatio="none" aria-hidden="true">
      <defs>
        <linearGradient id="bandGrad" x1="0" y1="0" x2="1" y2="1">
          <stop offset="0" stop-color="#b3232a"/>
          <stop offset="1" stop-color="#8e1418"/>
        </linearGradient>
      </defs>
      <path d="M620 0 H760 V434 H620 C700 330 700 110 620 0 Z" fill="url(#bandGrad)"/>
      <path d="M600 0 C690 110 690 330 615 434 L622 434 C700 330 702 110 612 0 Z" fill="#f37122"/>
    </svg>

    <div class="brand">
      <span class="brand-mark" role="img" aria-label="Company emblem"></span>
      <p class="brand-name"><span class="word">Valcorne</span><span class="tag">Health Care Marketing</span></p>
    </div>

    <div class="person">
      <p class="person-name">Marla Tenwick</p>
      <p class="person-role">CEO</p>
    </div>

    <ul class="contacts">
      <li><svg viewBox="0 0 24 24" aria-hidden="true"><path d="M6.6 10.8a15.1 15.1 0 0 0 6.6 6.6l2.2-2.2a1 1 0 0 1 1-.25 11.4 11.4 0 0 0 3.6.57 1 1 0 0 1 1 1V20a1 1 0 0 1-1 1A17 17 0 0 1 3 4a1 1 0 0 1 1-1h3.5a1 1 0 0 1 1 1c0 1.25.2 2.45.57 3.57a1 1 0 0 1-.25 1z"/></svg>(512)638-2974</li>
      <li><svg viewBox="0 0 24 24" aria-hidden="true"><path d="M3 5h18v14H3z M3 5l9 7 9-7" stroke="#fff" stroke-width="1.5"/></svg>marla@valcorne.com</li>
      <li><svg viewBox="0 0 24 24" aria-hidden="true"><circle cx="12" cy="12" r="10"/><path d="M2 12h20M12 2c3 3 3 17 0 20M12 2c-3 3-3 17 0 20" stroke="#fff" stroke-width="1.4" fill="none"/></svg>www.valcorne.com</li>
    </ul>
  </section>

  <section class="card card--back" aria-label="Business card back">
    <span class="brand-mark" role="img" aria-label="Company emblem"></span>
    <p class="brand-name"><span class="word">Valcorne</span><span class="tag">Health Care Marketing</span></p>
  </section>
</body>
</html>
```